TA BRAMLEY BUSINESS CARD DESIGN PROJECT

We need to utilize our logo that was expertly created on PixelHarbor and now need to match this with a business card design.

```html
<!DOCTYPE html>
<html lang="en">
<head>
<meta charset="utf-8">
<title>TA BRAMLEY Business Card</title>
<link href="https://fonts.googleapis.com/css2?family=Montserrat:wght@400;500;700;800&display=swap" rel="stylesheet">
<style>
  :root {
    --brand-blue: #1257ab;
    --card-white: #ffffff;
    --ink: #2b2b2b;
    --backdrop: #e9ebef;
  }
  html, body {
    margin: 0;
    padding: 0;
    width: 1200px;
    height: 834px;
    overflow: hidden;
    background: var(--backdrop);
    font-family: "Montserrat", sans-serif;
  }
  .canvas {
    position: relative;
    width: 1200px;
    height: 834px;
  }
  .card {
    position: absolute;
    top: 262px;
    width: 525px;
    height: 300px;
    overflow: hidden;
    box-shadow: 0 6px 18px rgba(0,0,0,0.15);
  }
  .card-front { left: 50px; background: var(--card-white); }
  .card-back  { left: 625px; background: var(--brand-blue); }

  .front-wave {
    position: absolute;
    left: 0; bottom: 0;
    width: 525px; height: 300px;
  }
  .front-wordmark {
    position: absolute;
    left: 40px; top: 70px;
    width: 200px;
    display: flex;
    align-items: center;
    gap: 10px;
    color: var(--brand-blue);
    font-weight: 800;
    font-size: 26px;
    letter-spacing: 3px;
    line-height: 1.1;
  }
  .front-wordmark .mark-dot {
    width: 18px; height: 18px;
    border-radius: 50%;
    background: var(--brand-blue);
    flex: none;
  }
  .divider {
    position: absolute;
    left: 262px; top: 52px;
    width: 1.5px; height: 168px;
    background: var(--brand-blue);
  }
  .contact {
    position: absolute;
    left: 282px; top: 52px;
    color: var(--ink);
  }
  .contact .name {
    margin: 0;
    font-weight: 800;
    font-size: 19px;
    color: var(--brand-blue);
    letter-spacing: 0.5px;
  }
  .contact .role {
    margin: 2px 0 14px;
    font-size: 13px;
    font-weight: 500;
  }
  .contact ul {
    list-style: none;
    margin: 0; padding: 0;
    font-size: 13px;
    font-weight: 500;
  }
  .contact li {
    display: flex;
    align-items: center;
    gap: 6px;
    margin-bottom: 3px;
  }
  .contact li svg { width: 12px; height: 12px; fill: var(--brand-blue); flex: none; }
  .contact .address {
    margin: 8px 0 0;
    font-size: 13px;
    font-weight: 500;
    line-height: 1.35;
  }

  .back-wordmark {
    position: absolute;
    inset: 0;
    display: flex;
    align-items: center;
    justify-content: center;
    gap: 16px;
    color: var(--card-white);
    font-weight: 800;
    font-size: 48px;
    letter-spacing: 6px;
  }
  .back-wordmark .mark-dot {
    width: 34px; height: 34px;
    border-radius: 50%;
    background: var(--card-white);
  }
</style>
</head>
<body>
<div class="canvas">

  <section class="card card-front" aria-label="Business card front">
    <svg class="front-wave" viewBox="0 0 525 300" aria-hidden="true">
      <path d="M0 190 C 90 215, 120 275, 300 285 C 400 290, 470 270, 525 205 L525 300 L0 300 Z" fill="var(--brand-blue)"/>
      <path d="M0 172 C 95 198, 125 262, 300 272 C 400 277, 470 257, 525 190" fill="none" stroke="var(--brand-blue)" stroke-width="2"/>
    </svg>

    <div class="front-wordmark">
      <span class="mark-dot"></span>
      <span>TA<br>BRAMLEY</span>
    </div>

    <div class="divider"></div>

    <div class="contact">
      <h1 class="name">NORA HALVIK</h1>
      <p class="role">Managing Director</p>
      <ul>
        <li>
          <svg viewBox="0 0 24 24"><path d="M6.6 10.8a15 15 0 006.6 6.6l2.2-2.2c.3-.3.7-.4 1-.2 1.1.4 2.3.6 3.6.6.6 0 1 .4 1 1V20c0 .6-.4 1-1 1A17 17 0 013 4c0-.6.4-1 1-1h3.5c.6 0 1 .4 1 1 0 1.3.2 2.5.6 3.6.1.3 0 .7-.2 1z"/></svg>
          123 456 789
        </li>
        <li>
          <svg viewBox="0 0 24 24"><rect x="6" y="2" width="12" height="20" rx="2"/></svg>
          123 456 789
        </li>
        <li>
          <svg viewBox="0 0 24 24"><path d="M2 5h20v14H2z M2 5l10 8 10-8" /></svg>
          info@tabramley.com
        </li>
        <li>
          <svg viewBox="0 0 24 24"><circle cx="12" cy="12" r="10"/></svg>
          www.tabramley.com
        </li>
      </ul>
      <p class="address">Your address, City<br>State, Zip 1234</p>
    </div>
  </section>

  <section class="card card-back" aria-label="Business card back">
    <div class="back-wordmark">
      <span class="mark-dot"></span>
      <span>TA BRAMLEY</span>
    </div>
  </section>

</div>
</body>
</html>
```